Computer consultant business card

Bexil Software is a newly started computer consulting company. It's a small one-man company that provides mostly Vornix applications but also websites in collaboration with designers. I'm running this company on the side of full time university studies.

I want the final design to be clean and memorable. Be creative! :)

Some inspiration:
http://www.pixelmarta.com/design/48317
http://www.pixelmarta.com/design/2739164/business-card-design-by-frostlynk
http://www.pixelmarta.com/design/604281/business-card-design-by-koralind-vestrabanu

See attachment for my company logo.
Updates

I would like to thank everyone for submitting! I'll need a couple of days to review and ultimately select a design.

Target Market(s)

Non-technical entrepreneurs and small companies.

Industry/Entity Type

University

Requirements
Must have
• My company logo.
In any way, both colors from my logo.
First- and last name, e-mail and phone number.
Double-sided design.
Nice to have
• Something creative with the symbol in my logo

```html
<!DOCTYPE html>
<html lang="en">
<head>
<meta charset="utf-8">
<title>Bexil Software – Business Card</title>
<link rel="stylesheet" href="https://fonts.googleapis.com/css2?family=Arimo:wght@400;700&family=Quicksand:wght@700&display=swap">
<style>
  :root {
    --brand-blue: #2b7df4;
    --brand-blue-light: #3d8af7;
    --brand-dark: #333132;
    --card-white: #ffffff;
    --backdrop: #e8e5e1;
    --text-font: "Arimo", Arial, sans-serif;
    --mark-font: "Quicksand", "Arimo", sans-serif;
  }
  * { box-sizing: border-box; margin: 0; padding: 0; }
  html, body {
    width: 1200px;
    height: 820px;
    overflow: hidden;
    background: var(--backdrop);
    font-family: var(--text-font);
  }
  .canvas {
    position: relative;
    width: 1200px;
    height: 820px;
  }
  .card {
    position: absolute;
    width: 560px;
    height: 320px;
    overflow: hidden;
    box-shadow: 0 6px 18px rgba(0, 0, 0, 0.18);
  }

  /* Front side */
  .card-front {
    left: 60px;
    top: 100px;
    background: var(--card-white);
  }
  .front-brand {
    position: absolute;
    left: 0;
    top: 0;
    width: 100%;
    height: 200px;
    display: flex;
    align-items: center;
    justify-content: center;
    gap: 22px;
  }
  .brand-dot {
    width: 78px;
    height: 78px;
    border-radius: 50%;
    background: var(--brand-blue);
  }
  .brand-name {
    font-family: var(--mark-font);
    font-weight: 700;
    font-size: 104px;
    line-height: 1;
    color: var(--brand-dark);
    letter-spacing: 1px;
    padding-bottom: 14px;
  }
  .name-band {
    position: absolute;
    left: 0;
    top: 200px;
    width: 100%;
    height: 38px;
    background: var(--brand-dark);
    border-bottom: 3px solid var(--card-white);
    color: var(--card-white);
    display: flex;
    align-items: center;
    justify-content: center;
    padding-left: 110px;
    font-size: 19px;
  }
  .name-first { font-weight: 700; margin-right: 5px; }
  .name-last { font-weight: 400; font-size: 16px; }
  .contact-panel {
    position: absolute;
    left: 0;
    top: 238px;
    width: 100%;
    height: 82px;
    background: var(--brand-blue);
    color: var(--card-white);
    display: flex;
    flex-direction: column;
    align-items: center;
    justify-content: center;
    gap: 10px;
    padding-left: 110px;
    font-size: 14px;
    letter-spacing: 0.5px;
  }
  .contact-row {
    display: flex;
    align-items: center;
    gap: 18px;
  }
  .contact-item {
    display: flex;
    align-items: center;
    gap: 6px;
  }
  .contact-icon {
    width: 12px;
    height: 12px;
    fill: var(--card-white);
  }
  .contact-address { font-size: 15px; letter-spacing: 1.5px; }

  /* Back side */
  .card-back {
    left: 590px;
    top: 410px;
    background: var(--brand-blue);
  }
  .back-pattern {
    position: absolute;
    inset: 0;
    background: linear-gradient(135deg, var(--brand-blue-light), var(--brand-blue));
  }
  .back-brand {
    position: absolute;
    inset: 0;
    display: flex;
    align-items: center;
    justify-content: center;
    font-family: var(--mark-font);
    font-weight: 700;
    font-size: 140px;
    color: var(--card-white);
    letter-spacing: 2px;
    padding-bottom: 18px;
  }
</style>
</head>
<body>
<main class="canvas">

  <section class="card card-front" aria-label="Business card front">
    <div class="front-brand">
      <span class="brand-dot" aria-hidden="true"></span>
      <span class="brand-name">bexil</span>
    </div>
    <div class="name-band">
      <span class="name-first">First Name,</span>
      <span class="name-last">Last Name</span>
    </div>
    <div class="contact-panel">
      <div class="contact-row">
        <span class="contact-item">
          <svg class="contact-icon" viewBox="0 0 24 24" aria-hidden="true">
            <path d="M6.6 10.8a15.1 15.1 0 0 0 6.6 6.6l2.2-2.2a1 1 0 0 1 1-.25 11.4 11.4 0 0 0 3.6.57 1 1 0 0 1 1 1V20a1 1 0 0 1-1 1A17 17 0 0 1 3 4a1 1 0 0 1 1-1h3.5a1 1 0 0 1 1 1c0 1.25.2 2.45.57 3.6a1 1 0 0 1-.25 1z"/>
          </svg>
          0987 654321
        </span>
        <span class="contact-item">
          <svg class="contact-icon" viewBox="0 0 24 24" aria-hidden="true">
            <path d="M2 5h20v14H2z M2 5l10 8 10-8" fill="none" stroke="#ffffff" stroke-width="2.4"/>
          </svg>
          info@bexil.com
        </span>
      </div>
      <div class="contact-address">00, Complex name, City, State 0042</div>
    </div>
  </section>

  <section class="card card-back" aria-label="Business card back">
    <div class="back-pattern" role="img" aria-label="Faint repeating pattern of the brand symbol on blue"></div>
    <div class="back-brand">bexil</div>
  </section>

</main>
</body>
</html>
```